Website images and banners needed to be created

We have a website we have not used in a few months that need updated sales banners and images resized for our web devs to upload and update. The site in question is w w w . p a l t r o n . c o m

Number of Pages Required

3 page

```html
<!DOCTYPE html>
<html lang="en">
<head>
<meta charset="utf-8">
<title>Paltron – Big Black Friday Event</title>
<link href="https://fonts.googleapis.com/css2?family=Lobster&family=Open+Sans:wght@400;600;700&display=swap" rel="stylesheet">
<style>
:root{
  --yellow:#ffd200;
  --yellow-soft:#ffe24d;
  --ink:#222222;
  --black:#111111;
  --red:#e3261b;
  --white:#ffffff;
  --grey-bg:#f4f4f4;
  --grey-line:#dddddd;
  --text-soft:#666666;
}
*{box-sizing:border-box;margin:0;padding:0}
html,body{width:940px;height:1200px;overflow:hidden;background:var(--white)}
body{position:relative;font-family:"Open Sans",Arial,sans-serif;color:var(--ink)}
.script{font-family:"Lobster",cursive;line-height:1.05}

/* ---------- website page ---------- */
.site{position:absolute;left:38px;top:80px;width:288px;height:1063px;background:var(--white);overflow:hidden}
.site-topbar{position:absolute;left:0;top:0;width:100%;height:6px;background:var(--black);color:var(--white);font-size:2.4px;display:flex;justify-content:flex-end;align-items:center;gap:5px;padding-right:16px}
.site-topbar .phone{font-size:3.6px;font-weight:700}
.site-header{position:absolute;left:0;top:11px;width:100%;height:16px}
.brand{position:absolute;left:50px;top:2px;display:flex;align-items:center;gap:3px;font-size:9px;font-weight:600;color:var(--ink)}
.brand-mark{width:6px;height:6px;background:var(--ink)}
.search{position:absolute;left:133px;top:4px;width:105px;height:8px;border:0.5px solid var(--grey-line);font-size:2.4px;color:#aaa;padding:2px 3px}
.search-btn{position:absolute;right:-1px;top:-1px;width:9px;height:8px;background:var(--black)}
.cart{position:absolute;left:272px;top:6px}
.site-nav{position:absolute;left:0;top:30px;width:100%;display:flex;justify-content:center;gap:5px;font-size:3px;font-weight:600}
.site-rule{position:absolute;left:0;top:38px;width:100%;height:1px;background:var(--yellow)}
.site-main{position:absolute;left:0;top:40px;width:100%;height:927px;background:var(--grey-bg)}
.trust{position:absolute;left:19px;top:5px;width:250px;display:flex;justify-content:space-between}
.trust-item{display:flex;align-items:center;gap:3px;background:var(--white);padding:2px 3px;width:58px;height:13px}
.trust-item b{display:block;font-size:2.6px;font-weight:400}
.trust-item i{display:block;font-size:2.1px;font-style:normal;color:#999}
.site-hero{position:absolute;left:0;top:23px;width:288px;height:140px;background:var(--ink);overflow:hidden}
.site-hero .title{position:absolute;left:0;width:150px;top:18px;text-align:center;color:var(--white);font-size:13.5px}
.site-hero .sub{position:absolute;left:0;width:150px;top:56px;text-align:center;color:var(--white);font-size:4.6px}
.site-hero .offer{position:absolute;left:40px;top:73px;width:75px;height:46px;border:1px solid var(--white);color:var(--white)}
.offer .upto{position:absolute;font-weight:400;color:var(--yellow)}
.offer .big{position:absolute;font-weight:700;line-height:1}
.offer .pct{position:absolute;font-weight:700;color:var(--yellow);line-height:1}
.offer .off{position:absolute;line-height:1}
.offer .every{position:absolute;line-height:1}
.site-hero .offer .upto{left:9px;top:4px;font-size:5.5px}
.site-hero .offer .big{left:19px;top:10px;font-size:22px}
.site-hero .offer .pct{left:46px;top:10px;font-size:11px}
.site-hero .offer .off{left:47px;top:25px;font-size:5.5px}
.site-hero .offer .every{left:10px;top:34px;font-size:7px}
.site-hero svg{position:absolute;left:0;top:0}

.tiles{position:absolute;left:19px;top:163px;width:250px;height:103px}
.tile{position:absolute;display:flex;align-items:center;justify-content:center;text-align:center;color:var(--white);font-size:3.6px;line-height:1.2}
.tile span{background:rgba(0,0,0,0.35);width:100%;padding:2px}
.tile.big{left:0;top:0;width:122px;height:103px;background:linear-gradient(160deg,#b8ab97,#8e7f6c 55%,#6d6157)}
.tile.big span{font-size:5.5px;padding:4px}
.t1{left:127px;top:0;width:60px;height:49px;background:linear-gradient(#e8e8e8,#9d9d9d)}
.t2{left:190px;top:0;width:60px;height:49px;background:linear-gradient(135deg,#8b8f9a,#6a4a7a)}
.t3{left:127px;top:54px;width:60px;height:49px;background:linear-gradient(#5c5c5c,#1e1e1e)}
.t4{left:190px;top:54px;width:60px;height:49px;background:linear-gradient(#a9a9a9,#3a2f2a)}

.section-title{position:absolute;left:0;top:280px;width:100%;text-align:center;font-size:4.6px;font-weight:400;color:#555}
.grid{position:absolute;left:19px;top:294px;width:250px;display:grid;grid-template-columns:repeat(4,60px);column-gap:3px;row-gap:9px}
.card{background:var(--white);height:95px;text-align:center;font-size:2.5px;line-height:1.25;color:var(--text-soft)}
.card .pic{position:relative;height:58px;overflow:hidden;background:linear-gradient(#e9e9e9,#b9b9b9)}
.card .pic.dark{background:linear-gradient(#8a8a8a,#2d2d2d)}
.card .pic.room{background:linear-gradient(#cfc7bd,#8d8377)}
.card .ribbon{position:absolute;left:-9px;top:6px;width:32px;height:4px;background:var(--black);transform:rotate(-45deg);color:var(--white);font-size:1.8px;line-height:4px;text-align:center}
.card .name{height:11px;padding:3px 4px 0}
.card .tag{margin:1px auto 0;width:46px;height:3.6px;font-size:2.2px;line-height:3.6px}
.card .tag.dark{background:var(--ink);color:var(--white)}
.card .tag.yel{background:var(--yellow);color:var(--ink)}
.card .price{margin-top:3px;color:var(--red);font-size:2.8px}

.footer{position:absolute;left:19px;top:980px;width:250px;font-size:2.6px;color:#555;line-height:2.9}
.footer h4{font-size:2.2px;letter-spacing:0.4px;font-weight:400;margin-bottom:1px}
.foot-col{position:absolute;top:0}
.pay{position:absolute;left:170px;top:5px;width:80px}
.pay-row{display:flex;gap:2px;justify-content:flex-end;margin-bottom:15px}
.pay-chip{width:9px;height:5px;background:#c9c9c9;border-radius:1px}
.pay-chip.wide{width:14px;background:#333}
.site-bottom{position:absolute;left:0;top:1049px;width:100%;height:14px;background:var(--black);color:var(--white);font-size:2.2px;padding:5px 19px}

/* ---------- banners ---------- */
.banner{position:absolute;left:376px;width:522px;height:250px;overflow:hidden}
.banner svg.bg{position:absolute;left:0;top:0}
.banner .title{position:absolute;text-align:center;font-size:25px}
.banner .sub{position:absolute;text-align:center;font-size:9.5px}

.b-star{top:182px}
.b-star .title{left:18px;top:70px;width:200px;color:var(--black)}
.b-star .sub{left:18px;top:136px;width:200px;color:var(--black)}
.b-star .offer{position:absolute;left:235px;top:48px;width:120px;height:80px;color:var(--white)}
.b-star .offer .upto{left:0;top:0;font-size:11px;color:var(--white)}
.b-star .offer .big{left:18px;top:10px;font-size:44px}
.b-star .offer .pct{left:73px;top:9px;font-size:21px;color:var(--white)}
.b-star .offer .off{left:75px;top:36px;font-size:11px}
.b-star .offer .every{left:0;top:56px;font-size:14px}

.b-dark{top:452px;background:var(--ink)}
.b-dark .title{left:20px;top:34px;width:230px;color:var(--white)}
.b-dark .sub{left:20px;top:100px;width:230px;color:var(--white)}
.b-dark .offer{position:absolute;left:72px;top:130px;width:135px;height:82px;border:2px solid var(--white);color:var(--white)}
.b-dark .offer .upto{left:15px;top:6px;font-size:11px}
.b-dark .offer .big{left:33px;top:16px;font-size:42px}
.b-dark .offer .pct{left:83px;top:16px;font-size:21px}
.b-dark .offer .off{left:83px;top:44px;font-size:11px}
.b-dark .offer .every{left:18px;top:60px;font-size:14px}

.b-yellow{top:727px;background:linear-gradient(135deg,var(--yellow-soft),var(--yellow))}
.b-yellow .title{left:320px;top:38px;width:170px;color:var(--black)}
.b-yellow .sub{left:320px;top:98px;width:170px;color:var(--black)}
.b-yellow .offer{position:absolute;left:378px;top:128px;width:110px;height:70px;color:var(--red)}
.b-yellow .offer .upto{left:0;top:0;font-size:11px;color:var(--red)}
.b-yellow .offer .big{left:18px;top:10px;font-size:42px}
.b-yellow .offer .pct{left:68px;top:9px;font-size:21px;color:var(--red)}
.b-yellow .offer .off{left:68px;top:36px;font-size:11px}
.b-yellow .offer .every{left:0;top:53px;font-size:14px}
</style>
</head>
<body>

<section class="site" aria-label="Paltron home page">
  <div class="site-topbar"><span>Contact Us</span><span>sales@paltron.com</span><span class="phone">0200 555 0142</span></div>

  <header class="site-header">
    <div class="brand"><span class="brand-mark"></span>paltron.com</div>
    <div class="search">Search for products...<span class="search-btn"></span></div>
    <svg class="cart" width="6" height="5" viewBox="0 0 12 10"><path d="M0 1h2l2 6h6l1.5-4H3" fill="none" stroke="#222" stroke-width="1.2"/><circle cx="5" cy="9" r="1" fill="#222"/><circle cx="9" cy="9" r="1" fill="#222"/></svg>
  </header>

  <nav class="site-nav"><span>Leather Beds</span><span>Mattresses</span><span>Divans</span><span>Fabric Beds</span><span>Metal Beds</span><span>Kids Beds</span><span>Bunk Beds</span><span>Wooden Beds</span><span>Rattan</span></nav>
  <div class="site-rule"></div>

  <main class="site-main">
    <div class="trust">
      <div class="trust-item"><svg width="12" height="8" viewBox="0 0 24 16"><rect x="1" y="3" width="13" height="8" fill="none" stroke="#222"/><path d="M14 6h5l3 3v2h-8z" fill="none" stroke="#222"/><circle cx="6" cy="13" r="2" fill="none" stroke="#222"/><circle cx="18" cy="13" r="2" fill="none" stroke="#222"/></svg><div><b>FREE FAST DELIVERY</b><i>Selected postcodes</i></div></div>
      <div class="trust-item"><svg width="8" height="9" viewBox="0 0 16 18"><rect x="2" y="8" width="12" height="9" fill="#222"/><path d="M5 8V5a3 3 0 0 1 6 0v3" fill="none" stroke="#222" stroke-width="2"/></svg><div><b>SECURE CHECKOUT</b><i>Buy with confidence</i></div></div>
      <div class="trust-item"><svg width="10" height="8" viewBox="0 0 20 16"><rect x="2" y="1" width="16" height="10" fill="none" stroke="#222"/><path d="M2 1l16 10M18 1L2 11M10 1v10M2 6h16" stroke="#222"/><path d="M2 1v15" stroke="#222"/></svg><div><b>MADE IN THE UK</b><i>Mattress + divans</i></div></div>
      <div class="trust-item"><svg width="9" height="9" viewBox="0 0 18 18"><path d="M12 2a8 8 0 1 0 4 13A7 7 0 0 1 12 2z" fill="none" stroke="#222" stroke-width="1.3"/></svg><div><b>30 NIGHT COMFORT</b><i>Guarantee</i></div></div>
    </div>

    <div class="site-hero">
      <svg width="288" height="140" viewBox="0 0 288 140">
        <polygon points="158,0 288,0 288,140 130,140" fill="#c7c1b8"/>
        <polygon points="152,0 158,0 130,140 124,140" fill="var(--yellow)"/>
      </svg>
      <div role="img" aria-label="Photo of a black upholstered bed with a white mattress in a bright bedroom" style="position:absolute;left:160px;top:0;width:128px;height:140px;background:linear-gradient(170deg,#e4ded5,#b9b1a6 60%,#3a3a3a 85%);clip-path:polygon(0 0,100% 0,100% 100%,-22% 100%)"></div>
      <div class="title script">The Big Black<br>Friday Event</div>
      <div class="sub">Sale Must End Soon</div>
      <div class="offer"><span class="upto">UP TO</span><span class="big">70</span><span class="pct">%</span><span class="off">OFF</span><span class="every">EVERY THING</span></div>
    </div>

    <div class="tiles">
      <div class="tile big" role="img" aria-label="Photo of a white metal bed in a room with a window"><span>Up to 70% off on Fabric Beds</span></div>
      <div class="tile t1" role="img" aria-label="Photo of a stack of mattresses"><span>Up to 70% off on Mattresses</span></div>
      <div class="tile t2" role="img" aria-label="Photo of a divan bed with purple throw"><span>Up to 70% off on Divan Beds</span></div>
      <div class="tile t3" role="img" aria-label="Photo of a black leather bed"><span>Up to 70% off on Leather Beds</span></div>
      <div class="tile t4" role="img" aria-label="Photo of a rattan garden set"><span>Up to 70% off on Rattan Sets</span></div>
    </div>

    <h2 class="section-title">Check out our top selling items</h2>

    <div class="grid">
      <div class="card"><div class="pic" role="img" aria-label="Mattress photo"><span class="ribbon">UP TO 70% OFF</span></div><div class="name">Orla Memory Foam Medium Mattress</div><div class="tag dark">Choice Of Colours &amp; Sizes</div><div class="tag yel">Next Day Delivery / Select Day</div><div class="price">From only £65.00</div></div>
      <div class="card"><div class="pic" role="img" aria-label="Mattress photo"><span class="ribbon">UP TO 70% OFF</span></div><div class="name">Dalby Dual Spring Foam Mattress</div><div class="tag dark">Choice Of Colours &amp; Sizes</div><div class="tag yel">Next Day Delivery / Select Day</div><div class="price">From only £69.95</div></div>
      <div class="card"><div class="pic" role="img" aria-label="Mattress photo"><span class="ribbon">UP TO 70% OFF</span></div><div class="name">Pocket 1500 Spring Foam Mattress</div><div class="tag dark">Choice Of Colours &amp; Sizes</div><div class="tag yel">Next Day Delivery / Select Day</div><div class="price">From only £119.00</div></div>
      <div class="card"><div class="pic room" role="img" aria-label="Mattress photo"><span class="ribbon">UP TO 70% OFF</span></div><div class="name">Natural 2000 Pocket Spring Mattress</div><div class="tag dark">Choice Of Colours &amp; Sizes</div><div class="tag yel">Next Day Delivery / Select Day</div><div class="price">From only £185.90</div></div>

      <div class="card"><div class="pic" role="img" aria-label="Mattress photo"><span class="ribbon">UP TO 70% OFF</span></div><div class="name">Ortho 2600 Spring Foam Mattress</div><div class="tag dark">Choice Of Colours &amp; Sizes</div><div class="tag yel">Next Day Delivery / Select Day</div><div class="price">From only £189.00</div></div>
      <div class="card"><div class="pic room" role="img" aria-label="Divan bed photo"><span class="ribbon">UP TO 70% OFF</span></div><div class="name">Harlow Divan Bed Set with Mattress</div><div class="tag dark">Choice Of Colours &amp; Sizes</div><div class="tag yel">Next Day Delivery / Select Day</div><div class="price">From only £155.00</div></div>
      <div class="card"><div class="pic" role="img" aria-label="Divan bed photo"><span class="ribbon">UP TO 70% OFF</span></div><div class="name">Velvet Divan Set with Fabric Headboard</div><div class="tag dark">Choice Of Colours &amp; Sizes</div><div class="tag yel">Next Day Delivery / Select Day</div><div class="price">From only £169.00</div></div>
      <div class="card"><div class="pic dark" role="img" aria-label="Divan bed photo"><span class="ribbon">UP TO 70% OFF</span></div><div class="name">Damask Cotton Divan Bed Set</div><div class="tag dark">Choice Of Colours &amp; Sizes</div><div class="tag yel">Next Day Delivery / Select Day</div><div class="price">From only £139.00</div></div>

      <div class="card"><div class="pic room" role="img" aria-label="Divan bed photo"><span class="ribbon">UP TO 70% OFF</span></div><div class="name">Ashby Divan Bed with Headboard</div><div class="tag dark">Choice Of Colours &amp; Sizes</div><div class="tag yel">Next Day Delivery / Select Day</div><div class="price">From only £199.00</div></div>
      <div class="card"><div class="pic" role="img" aria-label="Divan bed photo"><span class="ribbon">UP TO 70% OFF</span></div><div class="name">Grey Fabric Divan Set with Foam</div><div class="tag dark">Choice Of Colours &amp; Sizes</div><div class="tag yel">Next Day Delivery / Select Day</div><div class="price">From only £119.00</div></div>
      <div class="card"><div class="pic" role="img" aria-label="Divan bed photo"><span class="ribbon">UP TO 70% OFF</span></div><div class="name">Tufted Fabric Divan Bed Set</div><div class="tag dark">Choice Of Colours &amp; Sizes</div><div class="tag yel">Next Day Delivery / Select Day</div><div class="price">From only £149.00</div></div>
      <div class="card"><div class="pic room" role="img" aria-label="Divan bed photo"><span class="ribbon">UP TO 70% OFF</span></div><div class="name">Pillow Top Divan Bed with Drawers</div><div class="tag dark">Choice Of Colours &amp; Sizes</div><div class="tag yel">Next Day Delivery / Select Day</div><div class="price">From only £219.00</div></div>

      <div class="card"><div class="pic room" role="img" aria-label="Metal bed photo"><span class="ribbon">UP TO 70% OFF</span></div><div class="name">Crystal Metal Bed Frame</div><div class="tag dark">Choice Of Colours &amp; Sizes</div><div class="tag yel">Next Day Delivery / Select Day</div><div class="price">From only £109.99</div></div>
      <div class="card"><div class="pic" role="img" aria-label="Metal bed photo"><span class="ribbon">UP TO 70% OFF</span></div><div class="name">White Metal Bed Frame</div><div class="tag dark">Choice Of Colours &amp; Sizes</div><div class="tag yel">Next Day Delivery / Select Day</div><div class="price">From only £139.00</div></div>
      <div class="card"><div class="pic" role="img" aria-label="Fabric bed photo"><span class="ribbon">UP TO 70% OFF</span></div><div class="name">Grey Fabric Bed Frame</div><div class="tag dark">Choice Of Colours &amp; Sizes</div><div class="tag yel">Next Day Delivery / Select Day</div><div class="price">From only £89.00</div></div>
      <div class="card"><div class="pic" role="img" aria-label="Ottoman bed photo"><span class="ribbon">UP TO 70% OFF</span></div><div class="name">Ottoman Gas Lift Fabric Bed</div><div class="tag dark">Choice Of Colours &amp; Sizes</div><div class="tag yel">Next Day Delivery / Select Day</div><div class="price">From only £139.00</div></div>

      <div class="card"><div class="pic room" role="img" aria-label="Ottoman bed photo"><span class="ribbon">UP TO 70% OFF</span></div><div class="name">Ottoman Lift Storage Bed</div><div class="tag dark">Choice Of Colours &amp; Sizes</div><div class="tag yel">Next Day Delivery / Select Day</div><div class="price">From only £169.00</div></div>
      <div class="card"><div class="pic dark" role="img" aria-label="Fabric bed photo"><span class="ribbon">UP TO 70% OFF</span></div><div class="name">Modern Grey Fabric Bed Frame</div><div class="tag dark">Choice Of Colours &amp; Sizes</div><div class="tag yel">Next Day Delivery / Select Day</div><div class="price">From only £119.00</div></div>
      <div class="card"><div class="pic dark" role="img" aria-label="Metal bed photo"><span class="ribbon">UP TO 70% OFF</span></div><div class="name">Black Metal Bed</div><div class="tag dark">Choice Of Colours &amp; Sizes</div><div class="tag yel">Next Day Delivery / Select Day</div><div class="price">From only £99.95</div></div>
      <div class="card"><div class="pic dark" role="img" aria-label="Leather bed photo"><span class="ribbon">UP TO 70% OFF</span></div><div class="name">Modern Leather Bed</div><div class="tag dark">Choice Of Colours &amp; Sizes</div><div class="tag yel">Next Day Delivery / Select Day</div><div class="price">From only £155.00</div></div>

      <div class="card"><div class="pic dark" role="img" aria-label="Leather bed photo"><span class="ribbon">UP TO 70% OFF</span></div><div class="name">Storage 4 Drawer Sleigh Bed</div><div class="tag dark">Choice Of Colours &amp; Sizes</div><div class="tag yel">Next Day Delivery / Select Day</div><div class="price">From only £175.00</div></div>
      <div class="card"><div class="pic dark" role="img" aria-label="Leather bed photo"><span class="ribbon">UP TO 70% OFF</span></div><div class="name">Modern Leather Bed Frame</div><div class="tag dark">Choice Of Colours &amp; Sizes</div><div class="tag yel">Next Day Delivery / Select Day</div><div class="price">From only £89.00</div></div>
      <div class="card"><div class="pic dark" role="img" aria-label="Ottoman bed photo"><span class="ribbon">UP TO 70% OFF</span></div><div class="name">Ottoman Gas Lift Storage Bed</div><div class="tag dark">Choice Of Colours &amp; Sizes</div><div class="tag yel">Next Day Delivery / Select Day</div><div class="price">From only £169.00</div></div>
      <div class="card"><div class="pic room" role="img" aria-label="Leather bed photo"><span class="ribbon">UP TO 70% OFF</span></div><div class="name">Leather Sleigh Bed Black or Brown</div><div class="tag dark">Choice Of Colours &amp; Sizes</div><div class="tag yel">Next Day Delivery / Select Day</div><div class="price">From only £129.00</div></div>
    </div>
  </main>

  <footer class="footer">
    <div class="foot-col" style="left:0"><h4>CUSTOMER CARE</h4>Contact us<br>About Us<br>FAQs<br>Delivery &amp; Returns<br>Terms &amp; Conditions<br>Privacy Policy</div>
    <div class="foot-col" style="left:85px"><h4>INFORMATION</h4>Free Next Day Delivery<br>Outstanding Products at Unbeatable Prices<br>Exclusive Daily Deals</div>
    <div class="pay">
      <div class="pay-row"><span class="pay-chip wide"></span><span class="pay-chip"></span><span class="pay-chip"></span><span class="pay-chip"></span><span class="pay-chip"></span></div>
      <div class="pay-row"><span class="pay-chip wide"></span><span class="pay-chip"></span><span class="pay-chip"></span><span class="pay-chip"></span></div>
    </div>
  </footer>
  <div class="site-bottom">© 2019 Paltron.com. All Rights Reserved.</div>
</section>

<section class="banner b-star">
  <div role="img" aria-label="Soft-focus photo of a white bed in a bedroom with lamps, and a smiling woman pointing at the offer" style="position:absolute;inset:0;background:linear-gradient(180deg,#bdb5aa 0%,#d8d2ca 40%,#eeece9 70%,#d9d6d2 100%)"></div>
  <div aria-hidden="true" style="position:absolute;left:395px;top:60px;width:127px;height:190px;background:linear-gradient(180deg,#c8b4a0,#b9c0c8 60%,#a7adb4)"></div>
  <svg class="bg" width="522" height="250" viewBox="0 0 522 250">
    <polygon fill="var(--yellow)" points="290,10 306,52 348,30 340,70 390,66 352,96 378,124 336,126 342,168 306,148 290,180 270,146 236,166 240,128 200,130 226,100 196,74 240,70 232,30 272,52"/>
  </svg>
  <div class="title script">The Big Black<br>Friday Event</div>
  <div class="sub">Sale Must End Soon</div>
  <div class="offer"><span class="upto">UP TO</span><span class="big">70</span><span class="pct">%</span><span class="off">OFF</span><span class="every">EVERY THING</span></div>
</section>

<section class="banner b-dark">
  <div role="img" aria-label="Photo of a black upholstered bed with a white mattress in a bright bedroom" style="position:absolute;inset:0;background:linear-gradient(165deg,#e6e1da,#cfc8bf 55%,#2e2e2e 80%,#d9d3cb);clip-path:polygon(299px 0,522px 0,522px 250px,240px 250px)"></div>
  <svg class="bg" width="522" height="250" viewBox="0 0 522 250">
    <polygon fill="var(--yellow)" points="287,0 300,0 240,244 227,244"/>
  </svg>
  <div class="title script">The Big Black<br>Friday Event</div>
  <div class="sub">Sale Must End Soon</div>
  <div class="offer"><span class="upto">UP TO</span><span class="big">70</span><span class="pct">%</span><span class="off">OFF</span><span class="every">EVERY THING</span></div>
</section>

<section class="banner b-yellow">
  <div role="img" aria-label="Photo of a smiling woman lying on a white bed making a peace sign" style="position:absolute;inset:0;background:linear-gradient(160deg,#d9c2a8,#efe4d6 45%,#f7f5f2 75%,#e6e2dc);clip-path:polygon(0 0,272px 0,335px 120px,320px 250px,0 250px)"></div>
  <svg class="bg" width="522" height="250" viewBox="0 0 522 250">
    <polygon fill="var(--black)" points="330,120 342,112 388,250 338,250 312,150"/>
    <polygon fill="#4a5561" points="312,130 322,122 330,140 318,146"/>
  </svg>
  <div class="title script">The Big Black<br>Friday Event</div>
  <div class="sub">Sale Must End Soon</div>
  <div class="offer"><span class="upto">UP TO</span><span class="big">70</span><span class="pct">%</span><span class="off">OFF</span><span class="every">EVERY THING</span></div>
</section>

</body>
</html>
```